KRV Boltmaster Manufacturer New Web Design

We need a new theme designed for metal fastener manufacturing company, KRV Boltmaster Group, a $60M division of Marrowfield Forge Holdings, Inc. We manufacture screw, pins and washers to industrial customers (non-Automotive) such as HN Homeware, Paul Brenner, LUX, Venmora, etc. Our current website is www.boltmaster.example. We would like to stick with the same logo/color scheme, however, I'm aiming to modernize the website's look and feel.

Here are some of our competitor's websites:
- https://www.torvalink.example/
- http://glenrivet.example/
- http://www.harlowbuiltjoining.example/
- http://lugsandcustoms.example/
- http://www.dunmerebolt.example/

Target Market(s)

We primarily want to target engineers working in the following markets:
- Appliance (HN Homeware, Frostavel)
- Ag (Brenner, LUX)
- Recreational Vehicle (Venmora, Tundra Fox)
- Outdoor Power (Brellvik, Pask)

We secondarily want to target buyers working at the above markets as well as buyers at Fastener distributors such as Boltique, Parts Dynamics, Kessel Fordham.

Industry/Entity Type

Metal Forging

Number of Pages Required

1 page

Requirements
Must have
• For products: "Threaded" product as the primary focus. "Pins" product is the secondary focus, followed by all others.
• Please use same logo and color scheme as I do not plan to change.
Nice to have
• Highlight our featured proprietary products (pamphlets attached). KRV Boltmaster's GRIP-N, KelDrive, Boltmaster Coil, Avalanche.

```html
<!DOCTYPE html>
<html lang="en">
<head>
<meta charset="utf-8">
<title>KRV Boltmaster Group – Products</title>
<link rel="stylesheet" href="https://fonts.googleapis.com/css2?family=Open+Sans:wght@300;400;700&display=swap">
<style>
  :root{
    --band-blue:#1b5ea4;
    --accent-teal:#14a08e;
    --button-blue:#0a86d0;
    --body-grey:#555;
    --panel-tint:#f3f3f3;
    --white:#fff;
  }
  *{box-sizing:border-box;margin:0;padding:0}
  html,body{width:1200px;height:1200px;overflow:hidden;background:var(--white)}
  body{position:relative;font-family:"Open Sans",Arial,sans-serif}
  .tint,.band,.photo,.intro,.cta{position:absolute}
  .tint{background:var(--panel-tint)}
  .band{background:var(--band-blue);color:var(--white)}
  .band-title{position:absolute;font-weight:700;font-size:23px;letter-spacing:3px;top:9px}
  .band-sub{position:absolute;font-weight:300;font-size:15px;letter-spacing:1.5px;top:43px}
  .intro{width:360px}
  .intro h2{font-weight:400;font-size:16.5px;line-height:18px;color:var(--accent-teal);letter-spacing:.4px;margin-bottom:4px}
  .intro p{font-weight:400;font-size:11.2px;line-height:13.5px;color:var(--body-grey);letter-spacing:.3px}
  .cta{width:113px;height:37px;background:var(--button-blue);color:var(--white);font-size:12px;letter-spacing:.4px;display:flex;align-items:center;justify-content:center;text-decoration:none}
  .photo-pins{background:linear-gradient(180deg,#e6e6e8,#cfcfd1)}
  .photo-washers{background:linear-gradient(135deg,#8d8577,#5e564b 55%,#a49a88)}
  .photo-stampings{background:linear-gradient(160deg,#5a5a5a,#1e1e1e 55%,#6b6b6b)}
</style>
</head>
<body>

<!-- Pins -->
<section class="product product-pins">
  <div class="tint" style="left:139px;top:0;width:587px;height:134px"></div>
  <div class="band" style="left:601px;top:42px;width:599px;height:76px">
    <span class="band-title" style="left:148px">PINS</span>
    <span class="band-sub" style="left:227px">Secure, Removable Solution</span>
  </div>
  <div class="photo photo-pins" role="img" aria-label="Photo of two threaded pins with square heads" style="left:601px;top:118px;width:599px;height:225px"></div>
  <div class="intro" style="left:151px;top:102px">
    <h2>Our Pin business is the traditional<br>Wessel product line.</h2>
    <p>Since 1929, KRV Wessel Pins has been leading the industry in a variety of manufacturing processes performed in-house at significant cost savings to the customers. Our expertise covers: Cold heading, cross-hole drilling, grooving/shaving, CNC operations, roll forming, broaching, grinding, and lanyard production. These capabilities, along with our engineering staff, have allowed us to focus on working with customers to solve all of their fastener problems.</p>
  </div>
  <a class="cta" href="#" style="left:151px;top:276px">Explore</a>
</section>

<!-- Lock washers -->
<section class="product product-washers">
  <div class="tint" style="left:474px;top:412px;width:587px;height:136px"></div>
  <div class="band" style="left:0;top:456px;width:600px;height:75px">
    <span class="band-title" style="left:122px">LOCK WASHERS</span>
    <span class="band-sub" style="left:293px">Heavy duty application</span>
  </div>
  <div class="photo photo-washers" role="img" aria-label="Photo of a pile of helical spring lock washers" style="left:0;top:531px;width:600px;height:225px"></div>
  <div class="intro" style="left:715px;top:480px;width:345px">
    <h2>Historically, KRV Boltmaster Group’s Helical Spring Lock Washers have been among the most widely used anti-loosening components on the market.</h2>
    <p>The “Split” in the helical spring lock washer absorbs the initial driving torque and visually closes under normal bolt loading. KRV Boltmaster Group’s Helical Spring Lock Washers are trapezoidal in shape, which contributes to the further deflection and compression of the washer under load.</p>
  </div>
  <a class="cta" href="#" style="left:715px;top:664px">Explore</a>
</section>

<!-- Stampings -->
<section class="product product-stampings">
  <div class="tint" style="left:141px;top:832px;width:585px;height:136px"></div>
  <div class="band" style="left:601px;top:870px;width:599px;height:75px">
    <span class="band-title" style="left:142px">STAMPNIGS</span>
    <span class="band-sub" style="left:301px">Diverse and Unique</span>
  </div>
  <div class="photo photo-stampings" role="img" aria-label="Photo of chrome star-shaped stamped parts" style="left:601px;top:945px;width:599px;height:225px"></div>
  <div class="intro" style="left:151px;top:914px;width:380px">
    <h2>KRV Boltmaster Group is the largest,<br>most diverse and uniquely tooled<br>producer of stampings products in the world.</h2>
    <p>Since its 1923 invention of the Twisted Tooth Lock Washer, Boltmaster has continued to invent products that revolutionized the stampings industry. Such product inventions as the Square Cones, Spring Washers, Internal/External Lock Washers and Shaft Retainers are the finest anti-vibration, anti-loosening, mechanical fastening devices available today.</p>
  </div>
  <a class="cta" href="#" style="left:151px;top:1095px">Explore</a>
</section>

</body>
</html>
```